Construction material supplies company business card ****

1. Full company name “K T Masonry Works Ltd”
I am after a Business card design for the company as a whole. We are better known in Solomon Islands as “K T Masonry” for short.

We are a building materials supplier of
Ready Mixed Concrete, Bricks and Blocks,
Quarry products- gravel, aggregates, sand etc.
Cement distributor/retailer of reputable brands.
Other prefab concrete products. Culverts, wave breakers, concrete retaining blocks etc.

2. Competitive Advantage over Competition: Quality, efficient, professional, dependable, reliable

3. We want people to feel trust worthy, high quality, strong when they see our brand

5. No preference to color. Maybe more sturdy and corporate. Not fancy.

Industry/Entity Type

CONSTRUCTION SUPPLY

Contact Information for Business Card

Name, Position, office phone mob phone, email

Requirements
Must have
• the company logo
Nice to have
• would like to see a mixture of designs, of with logo only and also with simple graphic designs to bring out the company whilst still have the strong sturdy professional feeling

```html
<!DOCTYPE html>
<html lang="en">
<head>
<meta charset="utf-8">
<title>K T Masonry – Business Card</title>
<link href="https://fonts.googleapis.com/css2?family=Roboto:wght@400;500;700&family=Exo+2:wght@700&display=swap" rel="stylesheet">
<style>
  :root{
    --page:#2a2a2a;
    --navy:#1b3d62;
    --navy-deep:#173455;
    --blue-1:#37597f;
    --blue-2:#24456a;
    --band:rgba(14,38,68,.55);
    --paper:#e8e8e8;
    --paper-2:#d9d9d9;
    --ink-light:#eef1f5;
  }
  *{box-sizing:border-box;margin:0;padding:0}
  html,body{width:1200px;height:1138px;overflow:hidden}
  body{background:var(--page);font-family:"Roboto",sans-serif;position:relative}
  .card{position:absolute;width:620px;height:375px;border-radius:16px;overflow:hidden}
  .card--front{left:274px;top:186px;background:linear-gradient(135deg,var(--blue-1),var(--blue-2));color:var(--ink-light)}
  .card--back{left:276px;top:608px;background:radial-gradient(ellipse at 40% 40%,#f1f1f1,var(--paper) 55%,var(--paper-2));color:var(--navy)}
  .brand-title{position:absolute;left:0;right:0;top:70px;text-align:center;font-family:"Exo 2",sans-serif;font-weight:700;font-size:50px;letter-spacing:2px;color:var(--ink-light)}
  .pill{position:absolute;left:138px;width:348px;top:186px;height:40px;border-radius:20px;background:rgba(20,45,78,.75);border:1px solid rgba(255,255,255,.12);display:flex;align-items:center;justify-content:center;font-size:16px;z-index:2}
  .band{position:absolute;left:0;right:0;top:214px;height:78px;background:var(--band)}
  .line{position:absolute;left:0;right:0;text-align:center;font-size:16px;line-height:1}
  .back-mark{position:absolute;left:92px;top:96px;width:160px;display:flex;flex-direction:column;align-items:center;gap:14px}
  .back-mark .square{width:64px;height:64px;background:var(--navy)}
  .back-mark .name{font-size:24px;font-weight:500;color:var(--navy)}
  .person{position:absolute;left:312px;top:62px}
  .person h1{font-size:23px;font-weight:700;line-height:1.2}
  .person .role{font-size:17px;margin-top:2px}
  .contacts{position:absolute;left:312px;top:135px;list-style:none;font-size:17px}
  .contacts li{display:flex;align-items:center;height:26px}
  .contacts svg{width:16px;height:16px;margin-right:16px;fill:var(--navy)}
  .contacts .addr{padding-left:0}
  .rule{position:absolute;left:0;right:0;top:322px;height:5px;background:var(--navy)}
  .footer{position:absolute;left:0;right:0;top:333px;bottom:0;background:var(--navy-deep);color:var(--ink-light);display:flex;align-items:center;justify-content:center;font-size:17px;word-spacing:2px}
</style>
</head>
<body>
  <section class="card card--front">
    <div class="brand-title">K T MASONRY</div>
    <div class="band"></div>
    <div class="pill">We are a building materials supplier of</div>
    <p class="line" style="top:243px">Ready Mixed Concrete, Bricks and Blocks, Quarry Products</p>
    <p class="line" style="top:265px">Quarry Products:- Gravel, Aggregates, Sand Etc.</p>
    <p class="line" style="top:310px">Cement Distributor/Retailer of Reputable Brands.</p>
    <p class="line" style="top:334px">Other Concrete Products Culverts, Wave Breakers, Concrete Retaining Blocks</p>
  </section>

  <section class="card card--back">
    <div class="back-mark">
      <div class="square"></div>
      <div class="name">K T Masonry</div>
    </div>
    <div class="person">
      <h1>Daniel Porter</h1>
      <p class="role">Managing Director</p>
    </div>
    <ul class="contacts">
      <li><svg viewBox="0 0 16 16"><path d="M2 6c0-2 3-3 6-3s6 1 6 3v1h-3V6H5v1H2z M4 8h8l1 5H3z"/></svg>000 0000 0000</li>
      <li><svg viewBox="0 0 16 16"><path d="M1 4h14v9H1z M2 5l6 4 6-4" stroke="#e8e8e8" stroke-width="1"/></svg>daniel@ktmasonry.com</li>
      <li><svg viewBox="0 0 16 16"><circle cx="8" cy="8" r="6.5" fill="none" stroke="#1b3d62" stroke-width="1.3"/><path d="M1.5 8h13M8 1.5c-3 3-3 10 0 13M8 1.5c3 3 3 10 0 13" fill="none" stroke="#1b3d62" stroke-width="1.1"/></svg>www.ktmasonry.com</li>
      <li class="addr">18 Harbour Rd., Point Cruz,</li>
      <li class="addr">Honiara, SB 00100</li>
    </ul>
    <div class="rule"></div>
    <div class="footer">Quality &nbsp;|&nbsp; Efficient &nbsp;|&nbsp; Professional &nbsp;|&nbsp; Dependable &nbsp;|&nbsp; Reliable</div>
  </section>
</body>
</html>
```